Sell the dream! Property investment proposal document

We are looking for a proposal document which outlines our vision for property development. The purpose of the document is to raise investment from investors - sell the dream!
Brief summary:
Kestrel Dwellings Developments, is an emerging New Zealand property investment company with a focus on providing unique property investment opportunities.
Our expertise and capabilities in architectural modular homes provide us with a remarkable advantage in tackling the development of properties that are typically considered challenging, remote, or uniquely positioned.
Our specialization in this niche sector of property development not only sets us apart from competitors, but also paves the way for lucrative investment opportunities in the New Zealand property market.
Feel free to use any images from www.kestreldwellings.co.nz
Target Market(s)
investors for a unique property development opportunity
Industry/Entity Type
luxury property development in unique locations throughout New Zealand
Colors
Designer to choose only greyscale colors for use in the design.
Look and feel

```html
<!DOCTYPE html>
<html lang="en">
<head>
<meta charset="utf-8">
<title>Kestrel Dwellings – Investment Proposal</title>
<link rel="stylesheet" href="https://fonts.googleapis.com/css2?family=Jost:wght@300;400;500&display=swap">
<style>
:root{
  --board:#6c6d70;
  --board-light:#a4a5a8;
  --ink:#161617;
  --paper:#f4f4f4;
  --stone:#3a3a3c;
  --mist:#c9c9cb;
  --label:#111;
}
*{margin:0;padding:0;box-sizing:border-box}
html,body{width:1037px;height:1200px;overflow:hidden}
body{
  background:linear-gradient(180deg,var(--board) 0%,var(--board-light) 55%,var(--board) 100%);
  font-family:"Jost",sans-serif;
  position:relative;
}
.label{position:absolute;width:200px;text-align:center;font-size:15px;color:var(--label);font-weight:400}
.page{position:absolute;width:471px;height:333px;background:var(--ink);overflow:hidden;box-shadow:0 10px 12px -6px rgba(0,0,0,.45)}
.col-left{left:42px}.col-right{left:523px}
.row-1{top:58px}.row-2{top:437px}.row-3{top:814px}
.abs{position:absolute}
.photo{position:absolute}
.bar{position:absolute;border-radius:3px}
.bar.light{background:var(--paper)}
.bar.dark{background:var(--ink)}
.wordmark{position:absolute;font-weight:400;font-size:62px;letter-spacing:-2px;line-height:1}
.brand{position:absolute;color:var(--paper);font-weight:500;font-size:10px;line-height:1.1}
.heading{position:absolute;color:var(--paper);font-weight:500;font-size:21px;letter-spacing:.3px;line-height:1}
.body{position:absolute;color:var(--mist);font-weight:300;font-size:3.9px;line-height:1.55;text-align:justify}
.body p{margin-bottom:3px}
.contact{position:absolute;color:var(--paper);font-weight:300;text-align:right}
</style>
</head>
<body>

<div class="label" style="left:177px;top:30px">Back</div>
<div class="label" style="left:659px;top:30px">Front</div>
<div class="label" style="left:184px;top:413px">Page 2</div>
<div class="label" style="left:663px;top:413px">Page 1</div>
<div class="label" style="left:184px;top:790px">Page 4</div>
<div class="label" style="left:663px;top:790px">Page 3</div>

<!-- Back cover -->
<section class="page col-left row-1 back-cover">
  <div class="abs" style="left:0;top:96px;width:471px;height:94px;background:var(--paper)"></div>
  <div class="wordmark" style="left:16px;top:40px;color:var(--paper)">Kestrel</div>
  <div class="brand" style="left:312px;top:14px;font-size:10px">Kestrel<br>Dwellings</div>
  <div class="bar light" style="left:421px;top:12px;width:3px;height:24px"></div>
  <div class="contact" style="right:30px;top:58px;font-size:13px">Ph: 09 555 0142</div>
  <div class="contact" style="right:30px;top:79px;font-size:12.5px">Web: www.kestreldwellings.co.nz</div>
  <div class="photo" role="img" aria-label="Black-clad modular home on a white plinth with lawn, trees and blue sky" style="left:30px;top:111px;width:413px;height:206px;background:linear-gradient(180deg,#b8c6d0 0%,#8a9a86 45%,#2a2c2c 55%,#6f8a4a 80%,#7f9a52 100%)"></div>
  <div class="bar dark" style="left:325px;top:107px;width:122px;height:6px"></div>
  <div class="bar dark" style="left:441px;top:107px;width:6px;height:64px"></div>
  <div class="bar light" style="left:25px;top:200px;width:6px;height:121px"></div>
  <div class="bar light" style="left:25px;top:315px;width:66px;height:6px"></div>
</section>

<!-- Front cover -->
<section class="page col-right row-1 front-cover">
  <div class="abs" style="left:0;top:0;width:472px;height:96px;background:var(--paper)"></div>
  <div class="photo" role="img" aria-label="Cantilevered glass house on a coastal point at sunset over calm water" style="left:29px;top:35px;width:184px;height:266px;background:linear-gradient(180deg,#9fb3c6 0%,#c9cdd0 45%,#d9c49a 60%,#5a5c5c 75%,#6e6862 100%)"></div>
  <div class="bar dark" style="left:25px;top:30px;width:122px;height:6px"></div>
  <div class="bar dark" style="left:25px;top:30px;width:6px;height:64px"></div>
  <div class="bar light" style="left:210px;top:238px;width:6px;height:66px"></div>
  <div class="bar light" style="left:94px;top:298px;width:122px;height:6px"></div>
  <div class="wordmark" style="left:236px;top:42px;color:var(--ink)">Kestrel</div>
  <div class="abs" style="left:250px;top:185px;color:var(--mist);font-weight:300;font-size:21px;letter-spacing:4.5px">Sell the dream!</div>
  <div class="abs" style="left:63px;top:316px;color:var(--mist);font-weight:300;font-size:8px;letter-spacing:1px">www.kestreldwellings.co.nz</div>
  <div class="brand" style="left:386px;top:304px;font-size:8.5px">Kestrel<br>Dwellings</div>
  <div class="bar light" style="left:452px;top:303px;width:3px;height:22px"></div>
</section>

<!-- Page 2 -->
<section class="page col-left row-2 origins">
  <h2 class="heading" style="left:14px;top:20px">Business Origins</h2>
  <div class="body" style="left:14px;top:50px;width:197px">
    <p>Kestrel Dwellings Developments was established with the goal of transforming the property investment market in New Zealand by introducing an innovative approach that centers on architectural modular designs and streamlined project timelines.</p>
    <p>Driven by our enthusiasm for architecture and real estate, we have expanded our successful business model to not only offer financial opportunities for investors but also to expand on our passion for high-end architectural design.</p>
    <p>With a wealth of experience accumulated over the past six years in the construction and the property market, we are pivoting to focus solely on our property development initiatives, presenting completed Kestrel projects to the market, in exclusive locations.</p>
    <p>These projects will boast high-quality standards, meticulous attention to detail and landscaping, and creative design elements.</p>
    <p>By introducing completed Kestrel properties into the market, we aim to reach a wider audience, catering to individuals who prefer ready-to-occupy homes, over engaging in the design and construction process. This approach also simplifies the financing process for prospective buyers, as established properties are often preferred by financial lenders.</p>
  </div>
  <div class="photo" role="img" aria-label="Concrete dining room with timber table, black chairs and fireplace" style="left:224px;top:17px;width:232px;height:170px;background:linear-gradient(180deg,#b9bab8 0%,#7c7f7a 45%,#5a4a3e 60%,#2a2a2c 100%)"></div>
  <div class="bar light" style="left:219px;top:12px;width:122px;height:6px"></div>
  <div class="bar light" style="left:219px;top:12px;width:6px;height:62px"></div>
  <div class="bar light" style="left:454px;top:74px;width:6px;height:119px"></div>
  <div class="bar light" style="left:393px;top:187px;width:67px;height:6px"></div>
  <div class="photo" role="img" aria-label="Bright living room with white sectional sofa and low coffee table" style="left:15px;top:204px;width:441px;height:113px;background:linear-gradient(90deg,#8a8a86 0%,#cfcdc8 30%,#b9b5ae 60%,#6e6a64 100%)"></div>
  <div class="bar light" style="left:10px;top:199px;width:122px;height:6px"></div>
  <div class="bar light" style="left:10px;top:199px;width:6px;height:60px"></div>
  <div class="bar light" style="left:454px;top:256px;width:6px;height:65px"></div>
  <div class="bar light" style="left:338px;top:315px;width:122px;height:6px"></div>
</section>

<!-- Page 1 -->
<section class="page col-right row-2 overview">
  <h2 class="heading" style="left:32px;top:10px">Business Overview</h2>
  <div class="body" style="left:32px;top:34px;width:407px">
    <p>Kestrel Dwellings Developments, is an emerging New Zealand property investment company with a focus on providing unique property investment opportunities. Our expertise and capabilities in architectural modular homes provide us with a remarkable advantage in tackling the development of properties that are typically considered challenging, remote, or uniquely positioned. As a company, with 48 employees boasting a wealth of experience in handling complex architectural projects, making us well-equipped to navigate the intricacies and demands of such ventures. This advantage allows us to not only execute projects efficiently but also to deliver exceptional results within condensed time frames. By capitalizing on our ability to develop difficult, remote, or one-of-a-kind properties swiftly and effectively, Kestrel Dwellings Developments offers investors a rare chance to engage in projects that promise exceptional profitability in the New Zealand property market. Our specialization in this niche sector of property development not only sets us apart from competitors, but also paves the way for lucrative investment opportunities in the New Zealand property market.</p>
  </div>
  <div class="photo" role="img" aria-label="Dark timber modular cabin with deck and boardwalk on a grassy coastal hillside at dusk" style="left:15px;top:103px;width:441px;height:214px;background:linear-gradient(180deg,#a8b6c4 0%,#c4c6c4 25%,#2a2a2c 40%,#3c3a36 70%,#6a4a3a 100%)"></div>
  <div class="wordmark" style="left:30px;top:253px;color:#b8b8ba;font-size:54px">Kestrel</div>
  <div class="bar light" style="left:394px;top:98px;width:66px;height:6px"></div>
  <div class="bar light" style="left:454px;top:98px;width:6px;height:123px"></div>
  <div class="bar light" style="left:11px;top:200px;width:6px;height:121px"></div>
  <div class="bar light" style="left:11px;top:315px;width:66px;height:6px"></div>
</section>

<!-- Page 4 -->
<section class="page col-left row-3 financial">
  <h2 class="heading" style="left:16px;top:230px;transform:rotate(-90deg);transform-origin:left top;white-space:nowrap;top:230px;font-size:20px;width:0">Financial Summary</h2>
  <div class="body" style="left:43px;top:20px;width:120px;font-size:4.2px;line-height:2.1">
    <p>In terms of financial projections, with each development, we anticipate a profit of 10%-20% which will be project dependent.</p>
    <p>This growth is fueled by the increasing demand for unique property investments in New Zealand and our ability to deliver high-quality services to the market in a condensed time frame, with heavily controlled costs.</p>
    <p>With a solid business model and a dedicated team, we are confident in our ability to achieve success and establish Kestrel Dwellings Investments as a trusted name in the industry.</p>
    <p>New Zealand's property market has been experiencing steady growth over the years, making it an attractive destination for property investors. With its beautiful landscapes and strong economy, New Zealand offers a diverse range of investment opportunities for both local and international investors. The demand for quality properties in prime locations continues to rise, creating a favorable environment for property investment companies like ours that can lean on our modular benefits of being able to reach unique and remote locations.</p>
  </div>
  <div class="photo" role="img" aria-label="Timber-ceiling living space with skylights, oval dining table and sea view" style="left:172px;top:16px;width:284px;height:302px;background:linear-gradient(180deg,#6b4e36 0%,#a07a56 30%,#c9c9c4 55%,#8a8a80 70%,#4a3e34 100%)"></div>
  <div class="bar light" style="left:394px;top:11px;width:66px;height:6px"></div>
  <div class="bar light" style="left:454px;top:11px;width:6px;height:123px"></div>
  <div class="bar light" style="left:167px;top:197px;width:6px;height:126px"></div>
  <div class="bar light" style="left:167px;top:317px;width:122px;height:6px"></div>
  <div class="brand" style="left:64px;top:300px;font-size:9px">Kestrel<br>Dwellings</div>
  <div class="bar light" style="left:135px;top:299px;width:3px;height:24px"></div>
</section>

<!-- Page 3 -->
<section class="page col-right row-3 advantage">
  <div class="photo" role="img" aria-label="Covered outdoor lounge with white sofas, dark cladding and a potted plant" style="left:15px;top:20px;width:441px;height:205px;background:linear-gradient(90deg,#bdbdba 0%,#5a5c60 30%,#d4d4d2 55%,#3a3c40 80%,#2c3a2c 100%)"></div>
  <div class="bar light" style="left:11px;top:15px;width:66px;height:6px"></div>
  <div class="bar light" style="left:11px;top:15px;width:6px;height:123px"></div>
  <div class="bar light" style="left:454px;top:108px;width:6px;height:123px"></div>
  <div class="bar light" style="left:394px;top:225px;width:66px;height:6px"></div>
  <h2 class="heading" style="left:36px;top:238px;font-size:23px">Competitive Advantage</h2>
  <div class="body" style="left:36px;top:272px;width:270px">
    <p>Our competitive advantage lies in the uniqueness of our property investment opportunities. Unlike traditional real estate companies, we focus on offering properties that are not only profitable but also aesthetically pleasing and unique. By catering to the tastes of architecture lovers, we set ourselves apart from the competition and attract a niche market of customers who appreciate the artistry and design of our projects.</p>
    <p>Additionally, the streamlined and condensed timelines facilitated by our modular approach provide quicker returns on investment.</p>
  </div>
  <div class="brand" style="left:374px;top:291px;font-size:9px">Kestrel<br>Dwellings</div>
  <div class="bar light" style="left:444px;top:290px;width:3px;height:24px"></div>
</section>

</body>
</html>
```